Buch-Cover für Lichtblick gesucht
Zielgruppe
Wir sind eine Firma die hochwertige Fitnessprodukte produziert und vertreibt. Unsere Zielgruppe sind gesundheitsbewusste Frauen ab Mitte 20 bis open end, die hohe Ansprüche an sich selbst stellen und sich für das Thema Selbstoptimierung interessieren.
Aufgabenstellung
Es soll ein Hardcover gestaltet werden.
Buchtitel: Lichtblick, Untertitel: Ein Sommer voller Mut
Detaillierte Beschreibung der Projektanforderungen siehe Anhang Projektbeschreibung. Darüber hinaus bin ich auch für alternative Gestaltungs-Ideen offen.
Das Design soll der Käuferin folgendes vermitteln:
- Wertigkeit
- Positivität
und sie ein bisschen träumen lassen und natürlich neugierig auf den Inhalt machen.

```html
<!DOCTYPE html>
<html lang="de">
<head>
<meta charset="utf-8">
<title>Lichtblick – Buchcover</title>
<link rel="stylesheet" href="https://fonts.googleapis.com/css2?family=Courgette&family=Great+Vibes&family=Nothing+You+Could+Do&display=swap">
<style>
  :root {
    --sky-deep: #163f5c;
    --sky-teal: #2f6f78;
    --sky-haze: #b9a58c;
    --sunset-peach: #f2c9a6;
    --sunset-rose: #e6b2a4;
    --field-warm: #a88a6c;
    --interior-dark: #1d1f2a;
    --ink-white: #ffffff;
    --ink-red: #b3323b;
  }
  * { margin: 0; padding: 0; box-sizing: border-box; }
  html, body {
    width: 848px;
    height: 1200px;
    overflow: hidden;
    background: #ffffff;
  }
  .cover {
    position: relative;
    width: 848px;
    height: 1200px;
    overflow: hidden;
  }
  .cover-photo {
    position: absolute;
    inset: 0;
    background:
      radial-gradient(ellipse 60% 30% at 80% 58%, rgba(255,236,200,0.75), rgba(255,236,200,0) 70%),
      linear-gradient(180deg,
        var(--sky-deep) 0%,
        var(--sky-teal) 14%,
        var(--sky-haze) 28%,
        var(--sunset-peach) 42%,
        var(--sunset-rose) 52%,
        var(--field-warm) 66%,
        #5a4a44 76%,
        var(--interior-dark) 88%,
        #15161e 100%);
  }
  .author {
    position: absolute;
    top: 28px;
    left: 0;
    right: 0;
    text-align: center;
    font-family: "Courgette", cursive;
    font-size: 54px;
    color: var(--ink-white);
    letter-spacing: 0.5px;
  }
  .title {
    position: absolute;
    top: 170px;
    left: 0;
    right: 0;
    text-align: center;
    font-family: "Great Vibes", cursive;
    font-size: 178px;
    line-height: 1;
    color: var(--ink-white);
    text-shadow: 0 0 18px rgba(255,255,255,0.35);
  }
  .subtitle {
    position: absolute;
    top: 430px;
    left: 0;
    right: 0;
    text-align: center;
    font-family: "Nothing You Could Do", cursive;
    font-size: 40px;
    color: var(--ink-red);
  }
  .publisher {
    position: absolute;
    bottom: 52px;
    left: 0;
    right: 0;
    text-align: center;
    font-family: "Courgette", cursive;
    font-size: 28px;
    color: var(--ink-white);
  }
</style>
</head>
<body>
  <main class="cover">
    <div class="cover-photo" role="img" aria-label="Foto: Frau mit Sonnenbrille am Steuer eines offenen Cabrios auf einem Feldweg in der Abendsonne, von hinten gesehen, mit Lichtreflexen am Himmel"></div>
    <p class="author">Marte Quisselt</p>
    <h1 class="title">Lichtblick</h1>
    <p class="subtitle">Ein Sommer voller Mut</p>
    <p class="publisher">Sonnfeld</p>
  </main>
</body>
</html>
```